Meadowlark Hollow Candle Company needs a Label design

We need a label design for a new candle company based in Charleston South Carolina. Our mission is to provide people with candles that will fill any space with fragrances that are uplifting, comforting, fresh and will make any space feel like home. Our candles are aromatherapy, 100% soy wax, and hand poured (we would love for this to be indicated somewhere on the label). We would like to see a label that is modern, very clean and uses pastel colors like green, blush pink, mauve and blush blue. The final design should communicate peace, gratitude, hope, and happiness.

```html
<!DOCTYPE html>
<html lang="en">
<head>
<meta charset="utf-8">
<title>Meadowlark Hollow Candle Company – Honeysuckle Citrus Label</title>
<link rel="stylesheet" href="https://fonts.googleapis.com/css2?family=Mrs+Saint+Delafield&family=Philosopher&family=Playfair+Display:wght@700&family=Playfair+Display+SC&display=swap">
<style>
  :root {
    --page: #fefefe;
    --mint: #dafde0;
    --mint-soft: #e9fdec;
    --streak: #ffffff;
    --ink: #7a818a;
  }
  html, body {
    margin: 0;
    width: 1200px;
    height: 1102px;
    overflow: hidden;
    background: var(--page);
  }
  .label-art {
    display: block;
    width: 1200px;
    height: 1102px;
  }
  .logo-arc {
    font-family: "Philosopher", sans-serif;
    font-size: 40px;
    fill: var(--ink);
    letter-spacing: 2px;
  }
  .logo-word {
    font-family: "Playfair Display", serif;
    font-weight: 700;
    font-size: 84px;
    fill: var(--ink);
  }
  .scent-name {
    font-family: "Mrs Saint Delafield", cursive;
    font-size: 150px;
    fill: var(--ink);
  }
  .tagline {
    font-family: "Playfair Display SC", serif;
    font-size: 36px;
    fill: var(--ink);
  }
</style>
</head>
<body>
<svg class="label-art" viewBox="0 0 1200 1102" xmlns="http://www.w3.org/2000/svg">
  <defs>
    <linearGradient id="label-wash" x1="0" y1="0" x2="0" y2="1">
      <stop offset="0" stop-color="var(--mint-soft)"/>
      <stop offset="0.35" stop-color="var(--mint)"/>
      <stop offset="1" stop-color="var(--mint)"/>
    </linearGradient>
    <path id="arc-top" d="M 522 268 A 86 86 0 0 1 672 268"/>
    <path id="arc-bottom" d="M 538 382 A 80 80 0 0 0 676 382"/>
  </defs>

  <g class="label-body">
    <rect class="label-ground" x="137" y="181" width="920" height="695" rx="96"
          fill="url(#label-wash)" role="img"
          aria-label="Pale mint label ground with soft white brush-stroke marbling"/>
    <rect class="tagline-band" x="137" y="752" width="920" height="50" fill="var(--streak)" opacity="0.85"/>
  </g>

  <g class="logo-placeholder">
    <text class="logo-arc"><textPath href="#arc-top" startOffset="50%" text-anchor="middle">GOES</textPath></text>
    <text class="logo-word" x="600" y="350" text-anchor="middle" textLength="234" lengthAdjust="spacingAndGlyphs">LOGO</text>
    <text class="logo-arc"><textPath href="#arc-bottom" startOffset="50%" text-anchor="middle">HERE</textPath></text>
  </g>

  <g class="scent">
    <text class="scent-name" x="210" y="500" textLength="740" lengthAdjust="spacingAndGlyphs">Honeysuckle</text>
    <text class="scent-name" x="352" y="668" textLength="424" lengthAdjust="spacingAndGlyphs">Citrus</text>
  </g>

  <text class="tagline" x="215" y="787" textLength="776" lengthAdjust="spacingAndGlyphs">Aromatherapy - Hand Poured - 100% Soy Wax</text>
</svg>
</body>
</html>
```